Website for a company offering full serivce charging solutions for electric cars

The company "tanu-werk" (english: "tanu-works") offering all-in-one-solutions for charging infrastructure for electric mobility.

There are four products:
1- Wallboxes for single-family homes
2- Solutions for property devloper/-management for property parking space
3- All-in-one-charging solution for municipalities/communities
4- Solutions for tourism/hotels/holiday appartments

The Website structure:
1. Main Page
2.1. Product Page Single Homes
2.2. Product Page Property Management / Parking
2.3. Product Page Municipality
2.4. Product Page Tourism
3. Contact Form / Request for information
4. Imprint / Legal

The Website should be built on Wordpress with a powerful possibility to simply add/modify specific landing pages.

We would like you to implement the website later and also maintain it if possible, but we would be able to do minor modifications by ourselfs (for A/B-Testing)

The website should be clear and simple, easy to understand.
Target group is mainly B2C without deeper knowledge of that topic.

It should suggest, that we will provide a very simple way to get the charging infrastructure done.

We need a contact form, maybe we will use Hubspot later.

Attached you will find a draft of the main page and a landing page (for 2.2) - it is just the content, please ignore the design. We would love to let you create a suitable design.
Also you will find some drafts a bit different for the same story.

I added also a few stock photos, but they don't need to be used! If you have better ideas, you are welcome!

Industry/Entity Type

Charging/Electric mobility

Number of Pages Required

2 page

Font styles to use
Sans Serif

Requirements
Must have
• Based on Wordpress, and the designer should be able to implement it on Wordpress on a later step

```html
<!DOCTYPE html>
<html lang="de">
<head>
<meta charset="utf-8">
<title>tanu-werk.de – Wallbox für Ihr Zuhause</title>
<link rel="stylesheet" href="https://fonts.googleapis.com/css2?family=Krona+One&family=Poppins:wght@400;500;600&display=swap">
<style>
  :root{
    --pink:#f20ba9;
    --purple:#7a5cc2;
    --navy:#11152a;
    --ink:#151a2c;
    --text:#3a3f4e;
    --white:#ffffff;
    --grey:#eceef2;
  }
  *{box-sizing:border-box;margin:0;padding:0}
  html,body{width:1200px;height:2767px;overflow:hidden}
  body{position:relative;background:var(--white);font-family:"Poppins",sans-serif;color:var(--text)}
  .abs{position:absolute}
  h1,h2{font-family:"Krona One",sans-serif;font-weight:400;color:var(--ink);line-height:1.1;white-space:nowrap}

  /* header */
  .site-header{left:89px;top:22px;width:1022px;height:44px;display:flex;align-items:center;justify-content:space-between}
  .brand{display:flex;align-items:center;gap:12px;font-size:29px;font-weight:500;color:var(--ink)}
  .brand-dot{width:30px;height:30px;border-radius:50%;background:var(--pink)}
  .main-nav{display:flex;align-items:center;gap:30px;font-size:15px;color:var(--ink)}
  .main-nav .active{color:var(--pink)}
  .btn-outline{border:2px solid var(--pink);border-radius:22px;padding:9px 25px;font-size:13px;font-weight:600;color:var(--ink)}

  /* hero */
  .hero-art{left:660px;top:120px;width:480px;height:425px;border-radius:220px 220px 40px 40px;background:linear-gradient(90deg,#f4f4f6 0%,#f3d3eb 45%,#c9b6ec 100%)}
  .hero-text{left:89px;top:258px;width:545px;z-index:2}
  .hero-text h1{font-size:33px}
  .hero-lead{margin-top:14px;font-size:15.5px;line-height:1.55;color:var(--ink)}
  .hero-note{margin-top:6px;font-size:14px;line-height:1.6;width:500px}

  /* wave band */
  .wave{left:0;top:0}
  .circle-photo{left:72px;top:583px;width:490px;height:484px;border-radius:50%;background:var(--pink)}
  .circle-photo .inner{position:absolute;left:16px;top:0;width:474px;height:474px;border-radius:50%;background:linear-gradient(135deg,#9aa3b1 0%,#eef0f3 45%,#5c6573 100%)}
  .wishes{left:600px;top:672px;width:540px}
  .wishes h2{font-size:31px}
  .intro{margin:12px 0 10px;font-size:16px;color:var(--text)}
  .ticks{list-style:none}
  .ticks li{position:relative;padding-left:20px;font-size:14.5px;line-height:21px;margin-bottom:6px;color:var(--ink)}
  .ticks li::before{content:"";position:absolute;left:0;top:4px;width:13px;height:13px;border-radius:50%;background:var(--pink)}
  .ticks li::after{content:"";position:absolute;left:4px;top:7px;width:5px;height:3px;border-left:2px solid var(--white);border-bottom:2px solid var(--white);transform:rotate(-45deg)}

  .turnkey{left:89px;top:1377px;width:520px;color:var(--white)}
  .turnkey h2{font-size:31px;color:var(--white)}
  .turnkey .intro{color:var(--white);font-weight:500}
  .turnkey .ticks li{color:var(--white)}
  .turnkey .ticks li::before{background:var(--white)}
  .turnkey .ticks li::after{border-color:var(--pink)}
  .btn-solid{display:inline-block;margin-top:22px;background:var(--white);color:var(--ink);border-radius:22px;padding:12px 22px;font-size:12px;font-weight:600}
  .dots{left:620px;top:1615px;width:245px;height:250px;background-image:radial-gradient(circle,#ffffff 3px,transparent 3.5px);background-size:14px 14px;opacity:.9}
  .dots-under{left:620px;top:1830px;width:245px;height:35px;background-image:radial-gradient(circle,var(--purple) 3px,transparent 3.5px);background-size:14px 14px}
  .person-photo{left:660px;top:1305px;width:443px;height:527px;border-radius:12px;background:linear-gradient(160deg,#d9c6a4 0%,#f1eee9 40%,#4f6a8c 100%);box-shadow:0 30px 60px rgba(20,20,40,.18)}

  /* rent */
  .rent{left:200px;top:2024px;width:800px;text-align:center}
  .rent h2{font-size:33px}
  .rent p{margin:20px auto 0;width:680px;font-size:14.5px;line-height:22px}

  /* footer */
  .footer{left:0;top:2490px;width:1200px;text-align:center;color:var(--white)}
  .footer .brand{color:var(--white);justify-content:center;font-size:31px}
  .footer-nav{margin-top:28px;display:flex;justify-content:center;gap:23px;font-size:16px}
  .social{margin-top:24px;display:flex;justify-content:center;gap:8px}
  .social span{width:44px;height:44px;border-radius:50%;background:#232842}
  .footer-rule{position:absolute;left:89px;top:227px;width:1022px;height:1px;background:#2c3150}
  .copyright{position:absolute;left:0;top:245px;width:1200px;font-size:14px}
  .to-top{left:1130px;top:2699px;width:34px;height:34px;border-radius:50%;background:linear-gradient(135deg,var(--pink),var(--purple))}
  .to-top::after{content:"";position:absolute;left:14px;top:15px;width:6px;height:6px;border-left:2px solid #fff;border-top:2px solid #fff;transform:rotate(45deg)}
</style>
</head>
<body>

<header class="site-header abs">
  <div class="brand"><span class="brand-dot"></span>tanu-werk.de</div>
  <nav class="main-nav">
    <span class="active">Lösungen</span><span>Unternehmen</span><span>Services</span><span>Karriere</span>
    <span class="btn-outline">KONTAKT</span>
  </nav>
</header>

<div class="hero-art abs" role="img" aria-label="Illustration: pinkes Elektroauto an einer Ladesäule vor Windrädern"></div>
<section class="hero-text abs">
  <h1>Schnell und einfach zu<br>Ihrer privaten Wallbox</h1>
  <p class="hero-lead">Von der Bestandsaufnahme, über die Beratung möglicher Lösungen, bis zur Installation und Inbetriebnahme alles aus EINER Hand.</p>
  <p class="hero-note">Und wenn Sie wünschen, dann leihen wir Ihnen die Wallbox auch gerne gegen eine kleine Nutzungspauschale.</p>
</section>

<svg class="wave abs" width="1200" height="2767" viewBox="0 0 1200 2767" aria-hidden="true">
  <defs>
    <linearGradient id="band" x1="0" x2="1" y1="0" y2="0">
      <stop offset="0" stop-color="#f20ba9"/><stop offset="1" stop-color="#7a5cc2"/>
    </linearGradient>
  </defs>
  <path fill="url(#band)" d="M0,875 C180,850 300,1000 400,1150 C470,1240 560,1235 650,1175 C780,1090 880,1080 1000,1110 C1100,1135 1160,1170 1200,1180 L1200,1725 C1100,1740 1000,1720 900,1745 C700,1790 600,1895 380,1880 C200,1866 80,1830 0,1810 Z"/>
  <path fill="url(#band)" d="M0,2460 C150,2350 250,2242 380,2240 C600,2238 850,2480 1060,2480 C1130,2480 1170,2475 1200,2465 L1200,2767 L0,2767 Z"/>
  <path fill="#11152a" d="M0,2485 C150,2380 260,2272 390,2270 C600,2268 850,2490 1060,2492 C1130,2492 1170,2470 1200,2330 L1200,2767 L0,2767 Z"/>
</svg>

<div class="circle-photo abs" role="img" aria-label="Foto: Ladestecker an einer Ladesäule in Nahaufnahme"><div class="inner"></div></div>

<section class="wishes abs">
  <h2>Eine Wallbox nach<br>Ihren Wünschen</h2>
  <p class="intro">Wir finden gemeinsam die beste Lösung für Sie. Egal,</p>
  <ul class="ticks">
    <li>welches E-Mobil Sie betanken möchten</li>
    <li>welche Länge Ihr Anschlusskabel an Ihr Fahrzeug besitzen soll</li>
    <li>ob Sie einen eigenen Stromzähler mit besonders günstigem Strom anbinden möchten</li>
    <li>Sie eine bestehende Photovoltaikanlage integrieren möchten</li>
    <li>Sie eine monatliche Übersicht Ihrer ‚getankten' kWh haben möchten</li>
    <li>Sie zwecks der Abrechnung mit Ihrem Arbeitgeber oder als Selbstständiger verschiedene E-PKWs oder Ladevorgänge voneinander trennen wollen</li>
  </ul>
</section>

<section class="turnkey abs">
  <h2>Schlüsselfertig alles<br>aus einer Hand</h2>
  <p class="intro">Sie haben einen Ansprechpartner der für Sie</p>
  <ul class="ticks">
    <li>die Erstberatung übernimmt</li>
    <li>die Förderungsmöglichkeiten auslotet und ggf. beantragt</li>
    <li>die Installation mit allen benötigten Gewerken fachgerecht, sauber und schnell koordiniert</li>
    <li>die Inbetriebnahme und Einweisung sicherstellt</li>
    <li>die notwendige jährliche Wartung im Auge behält und organisiert</li>
    <li>bei Problemen oder Störungen zur Seite steht</li>
  </ul>
  <span class="btn-solid">JETZT ANGEBOT ANFORDERN</span>
</section>
<div class="dots abs"></div>
<div class="dots-under abs"></div>
<div class="person-photo abs" role="img" aria-label="Foto: Frau lädt ihr Elektroauto und hält ein Smartphone"></div>

<section class="rent abs">
  <h2>Auf Wunsch auch geliehen</h2>
  <p>Sie scheuen die hohen Investitionskosten? Dann bieten wir Ihnen eine Lösung bei der Sie die HW von uns mieten können. Selbst die Installation von bis zu 25 Meter Anschlusslänge bis zum nächsten Stromzähler und bei Objekten im Raum Oberbayern kostet Sie nichts, wenn Sie mit uns einen 24 Monats Mietvertrag über 50€ / Monat abschließen.</p>
</section>

<footer class="footer abs">
  <div class="brand"><span class="brand-dot"></span>tanu-werk.de</div>
  <nav class="footer-nav"><span>AGB</span><span>Datenschutzerklärung</span><span>Impressum</span><span>Kontakt</span><span>Karriere</span><span>FAQs</span></nav>
  <div class="social">
    <span role="img" aria-label="Soziales Netzwerk"></span>
    <span role="img" aria-label="Videokanal"></span>
    <span role="img" aria-label="Fotonetzwerk"></span>
  </div>
  <div class="footer-rule"></div>
  <p class="copyright">©tanu-werk GmbH</p>
</footer>
<div class="to-top abs" aria-label="Nach oben"></div>

</body>
</html>
```